website design for M&T Electric

A portfolio website for a high end commercial and residential electrical contracting company. The current site mandtelectric.example does not represent the current direction but the images in the gallery give you an idea of the work we do. Current logo will be uploaded shortly but is black text on white background.
Target Market(s)
General Contractors, Residential Home Owners, clients intersted in Velmora home automation.
Industry/Entity Type
Electrician
Coding
Coded - Design and coding required
Number of Pages Required
2 page
Font styles to use
Sans Serif
Colors
Designer to choose colors to be used in the design.
Requirements
Must have
- Portfolio section highlighting different service areas and products (Velmora Housepilot, etc)

```html
<!DOCTYPE html>
<html lang="en">
<head>
<meta charset="utf-8">
<title>M&amp;T Electric</title>
<link rel="stylesheet" href="https://fonts.googleapis.com/css2?family=Open+Sans:wght@400;600;700&family=Roboto:wght@400;500;700&display=swap">
<style>
:root{
  --orange:#f39c1a;
  --dark:#2f2f2f;
  --ink:#222;
  --text:#444;
  --muted:#777;
  --light:#f1f1f1;
  --white:#fff;
  --pill:#3a3a3a;
}
*{box-sizing:border-box;margin:0;padding:0}
html,body{width:1200px;height:3066px;overflow:hidden;background:var(--white)}
body{position:relative;font-family:"Open Sans",Arial,sans-serif;color:var(--text)}
.abs{position:absolute}
a{color:inherit;text-decoration:none}

/* header */
.site-header{position:absolute;left:0;top:0;width:1200px;height:65px;background:var(--white);z-index:5}
.brand-panel{position:absolute;left:0;top:0;width:430px;height:65px}
.brand-name{position:absolute;left:98px;top:12px;font-family:"Open Sans",sans-serif;font-weight:400;font-size:33px;color:var(--white);letter-spacing:1px}
.main-nav{position:absolute;top:22px;left:0;width:1200px;font-family:"Roboto",sans-serif;font-weight:500;font-size:16px;color:var(--ink)}
.main-nav a{position:absolute;white-space:nowrap}

/* hero */
.hero{position:absolute;left:0;top:65px;width:1200px;height:510px}
.hero-photo{position:absolute;inset:0;background:radial-gradient(ellipse at 55% 60%,#8a6a3c 0%,#4a4436 25%,#24303c 55%,#1a2430 100%)}
.hero-shade{position:absolute;inset:0;background:rgba(10,20,30,.35)}
.hero-title{position:absolute;top:125px;width:1200px;text-align:center;font-family:"Open Sans",sans-serif;font-weight:600;font-size:56px;color:var(--white);letter-spacing:1px}
.hero-lead{position:absolute;top:220px;left:250px;width:700px;text-align:center;font-weight:600;font-size:15px;line-height:28px;color:var(--white)}
.hero-curve{position:absolute;left:0;top:440px}
.arrow{position:absolute}

/* services */
.service{position:absolute;top:487px;width:340px;text-align:center}
.service-photo{width:212px;height:212px;border-radius:50%;margin:0 auto;border:9px solid #8a8a8a}
.service.active .service-photo{border-color:var(--orange)}
.service h3{margin-top:48px;font-family:"Roboto",sans-serif;font-weight:400;font-size:21px;color:var(--ink);letter-spacing:.5px}
.service.active h3{color:var(--orange)}
.service p{margin:14px auto 0;width:270px;font-size:13px;line-height:22px;color:var(--ink)}
.read-link{display:inline-block;margin-top:16px;font-family:"Roboto",sans-serif;font-weight:500;font-size:15px;color:var(--ink)}
.service.active .read-link{color:var(--orange)}

/* sections */
.band{position:absolute;left:0;width:1200px}
.section-title{position:absolute;width:1200px;text-align:center;font-family:"Roboto",sans-serif;font-weight:500;font-size:26px;color:var(--orange)}
.section-rule{position:absolute;left:560px;width:80px;height:2px;background:var(--orange)}

.about{top:936px;height:454px;background:var(--light)}
.about-copy{position:absolute;left:127px;top:132px;width:946px;text-align:center;font-size:13px;line-height:25px;color:var(--ink)}
.about-copy p+p{margin-top:14px}
.btn{position:absolute;top:362px;height:44px;font-family:"Open Sans",sans-serif;font-weight:600;font-size:14px;display:flex;align-items:center;justify-content:center}
.btn-primary{left:482px;width:109px;background:var(--orange);color:var(--white)}
.btn-outline{left:607px;width:109px;border:2px solid var(--ink);color:var(--ink);background:var(--white)}

.gallery{top:1390px;height:838px;background:var(--white)}
.filter{position:absolute;top:156px;width:186px;height:54px;border-radius:27px;background:var(--pill);color:var(--white);font-family:"Open Sans",sans-serif;font-weight:700;font-size:15px;display:flex;align-items:center;justify-content:center}
.filter.active{background:var(--orange)}
.tile{position:absolute;width:323px;height:233px;border:1px solid #ccc;padding:4px;background:var(--white)}
.tile div{width:100%;height:100%}

.testimonials{top:2228px;height:419px;background:var(--light)}
.testimonial{position:absolute;top:0;width:480px;height:419px}
.avatar{position:absolute;left:29px;top:178px;width:102px;height:102px;border-radius:50%;border:3px solid #2a4258;background:linear-gradient(#d9c7a8,#b89a72)}
.quote-mark{position:absolute;left:169px;top:148px}
.t-title{position:absolute;left:206px;top:196px;font-family:"Roboto",sans-serif;font-size:16px;color:var(--ink)}
.t-name{position:absolute;left:206px;top:223px;font-size:14px;color:var(--ink)}
.stars{position:absolute;left:206px;top:254px;font-size:16px;color:var(--orange);letter-spacing:1px}
.t-text{position:absolute;left:0;top:320px;width:470px;font-size:12.5px;line-height:25px;color:var(--muted)}

/* footer */
.site-footer{top:2647px;height:419px;background:var(--dark);color:var(--white)}
.footer-brand{position:absolute;left:102px;top:116px;font-family:"Open Sans",sans-serif;font-weight:400;font-size:38px;letter-spacing:1px;color:var(--white)}
.social{position:absolute;top:211px;width:36px;height:36px;border-radius:50%;border:2px solid var(--white)}
.v-rule{position:absolute;top:74px;width:1px;height:160px;background:#666}
.footer-head{position:absolute;top:52px;font-family:"Open Sans",sans-serif;font-weight:600;font-size:16px;color:var(--white)}
.footer-head::after{content:"";display:block;width:38px;height:2px;background:var(--white);margin-top:8px}
.quick-links{position:absolute;left:536px;top:112px;list-style:none;font-size:14px;line-height:25.5px}
.quick-links li::before{content:"› ";}
.contact-item{position:absolute;left:861px}
.contact-icon{position:absolute;left:0;top:0;width:40px;height:40px;border-radius:50%;border:2px solid var(--white)}
.contact-item svg{position:absolute;left:0;top:0}
.contact-label{position:absolute;left:55px;top:-4px;font-weight:700;font-size:14px;white-space:nowrap}
.contact-value{position:absolute;left:55px;top:20px;font-size:12.5px;line-height:19px;white-space:nowrap}
.footer-rule{position:absolute;left:100px;top:333px;width:1000px;height:1px;background:#666}
.copyright{position:absolute;top:365px;width:1200px;text-align:center;font-weight:600;font-size:13px}
</style>
</head>
<body>

<header class="site-header">
  <svg class="brand-panel" width="430" height="65" viewBox="0 0 430 65"><polygon points="0,0 430,0 395,65 0,65" fill="#1c1c1c"/></svg>
  <div class="brand-name">M&amp;T Electric</div>
  <nav class="main-nav">
    <a style="left:465px">HOME</a>
    <a style="left:568px">GALLERY</a>
    <a style="left:694px">SPECIALTY SERVICES</a>
    <a style="left:915px">ABOUT</a>
    <a style="left:1025px">CONTACT</a>
  </nav>
</header>

<section class="hero">
  <div class="hero-photo" role="img" aria-label="Evening view of a lit luxury home beside a pool"></div>
  <div class="hero-shade"></div>
  <h1 class="hero-title">M &amp; T ELECTRIC</h1>
  <p class="hero-lead">M &amp; T Electric is a full service electrical contracting shop. We offer commercial, residential, light industrial, and agricultural services.</p>
  <svg class="arrow" style="left:36px;top:205px" width="26" height="52" viewBox="0 0 26 52"><polyline points="24,2 2,26 24,50" fill="none" stroke="#fff" stroke-width="2"/></svg>
  <svg class="arrow" style="left:1138px;top:205px" width="26" height="52" viewBox="0 0 26 52"><polyline points="2,2 24,26 2,50" fill="none" stroke="#fff" stroke-width="2"/></svg>
  <svg class="hero-curve" width="1200" height="70" viewBox="0 0 1200 70"><path d="M0,100 L0,100 L0,95 C300,20 800,10 1200,50 L1200,70 L0,70 Z" fill="#fff"/><path d="M0,100 L0,100 L0,95 C300,20 800,10 1200,50 L1200,70 L0,70 Z" fill="#fff"/><path d="M0,92 Q350,40 600,30 T1200,52 L1200,70 L0,70 Z" fill="#fff"/></svg>
</section>

<article class="service" style="left:77px">
  <div class="service-photo" role="img" aria-label="Commercial building lit at night" style="background:radial-gradient(circle at 50% 60%,#c99a5a,#3a3a44 55%,#141a2a)"></div>
  <h3>COMMERCIAL</h3>
  <p>We're Velmora Housepilot and Velmora Motorized Shades certified, as well as an authorized Voltaris generator dealer.</p>
  <a class="read-link">READ MORE &nbsp;➔</a>
</article>
<article class="service active" style="left:435px">
  <div class="service-photo" role="img" aria-label="Warm lit residential interior with bookshelves" style="background:radial-gradient(circle at 50% 50%,#b47a3c,#5a3a20 60%,#2a1a10)"></div>
  <h3>RESIDENTIAL</h3>
  <p>We're Velmora Housepilot and Velmora Motorized Shades certified, as well as an authorized Voltaris generator dealer.</p>
  <a class="read-link">READ MORE &nbsp;➔</a>
</article>
<article class="service" style="left:783px">
  <div class="service-photo" role="img" aria-label="Living room with motorized window shades" style="background:linear-gradient(#cfd3d8,#8a8580 60%,#4a4440)"></div>
  <h3>LANDSCAPE</h3>
  <p>We're Velmora Housepilot and Velmora Motorized Shades certified, as well as an authorized Voltaris generator dealer.</p>
  <a class="read-link">READ MORE &nbsp;➔</a>
</article>

<section class="band about">
  <h2 class="section-title" style="top:52px">ABOUT US</h2>
  <div class="section-rule" style="top:92px"></div>
  <div class="about-copy">
    <p>M &amp; T Electric is a full service electrical contracting shop. We offer commercial, residential, light industrial, and agricultural services. We're Velmora Housepilot and Velmora Motorized Shades certified, as well as an authorized Voltaris generator dealer. We've served the Wood River and South Central Idaho area for over 18 years.</p>
    <p>We've served the Wood River and South Central Idaho area for over 18 years. M &amp; T Electric is a full service electrical contracting shop. We offer commercial, residential, light industrial, and agricul tural services. We're Velmora Housepilot and Velmora Motorized Shades certified, as well as an authorized Voltaris generator dealer.</p>
  </div>
  <a class="btn btn-primary">Read More</a>
  <a class="btn btn-outline">Contact Us</a>
</section>

<section class="band gallery">
  <h2 class="section-title" style="top:52px">OUR GALLERY</h2>
  <div class="section-rule" style="top:92px"></div>
  <a class="filter active" style="left:292px">COMMERCIAL</a>
  <a class="filter" style="left:507px">RESIDENTIAL</a>
  <a class="filter" style="left:721px">LANDSCAPE</a>
  <svg class="arrow" style="left:36px;top:475px" width="26" height="52" viewBox="0 0 26 52"><polyline points="24,2 2,26 24,50" fill="none" stroke="#888" stroke-width="2"/></svg>
  <svg class="arrow" style="left:1138px;top:475px" width="26" height="52" viewBox="0 0 26 52"><polyline points="2,2 24,26 2,50" fill="none" stroke="#888" stroke-width="2"/></svg>
  <div class="tile" style="left:100px;top:262px"><div role="img" aria-label="Stone commercial building with parked cars" style="background:linear-gradient(#5a8fd0 0%,#8ab0dc 35%,#8a7a66 40%,#6a5a48 85%,#777 100%)"></div></div>
  <div class="tile" style="left:439px;top:262px"><div role="img" aria-label="Multi-storey stone and timber building" style="background:linear-gradient(#4f86cf 0%,#90b4e0 30%,#8c6e56 36%,#5c4a3c 85%,#888 100%)"></div></div>
  <div class="tile" style="left:777px;top:262px"><div role="img" aria-label="Modern office building under blue sky" style="background:linear-gradient(#4b82d2 0%,#9dbde6 45%,#c9c2ae 50%,#9a9280 88%,#999 100%)"></div></div>
  <div class="tile" style="left:100px;top:511px"><div role="img" aria-label="Tan modern commercial building" style="background:linear-gradient(#4a7fd0 0%,#a6c3e8 25%,#c8a890 32%,#9a7a68 88%,#666 100%)"></div></div>
  <div class="tile" style="left:439px;top:511px"><div role="img" aria-label="Building beneath snowy mountain slope" style="background:linear-gradient(#8a7a88 0%,#b3a0b0 40%,#6a6070 55%,#5a5058 88%,#555 100%)"></div></div>
  <div class="tile" style="left:777px;top:511px"><div role="img" aria-label="Low building with mountains under purple sky" style="background:linear-gradient(#9a8ed0 0%,#c5b8e0 45%,#7a6e8a 62%,#4a4450 90%,#555 100%)"></div></div>
</section>

<section class="band testimonials">
  <h2 class="section-title" style="top:52px">OUR TESTIMONIALS</h2>
  <div class="section-rule" style="top:92px"></div>
  <div class="testimonial" style="left:100px">
    <div class="avatar" role="img" aria-label="Customer portrait"></div>
    <svg class="quote-mark" width="30" height="26" viewBox="0 0 30 26"><path d="M0,0h12v12l-6,14h-5l4-12h-5z M16,0h12v12l-6,14h-5l4-12h-5z" fill="#f39c1a"/></svg>
    <div class="t-title">GOOD SERVICE</div>
    <div class="t-name">Marisol</div>
    <div class="stars">★★★★☆</div>
    <p class="t-text">Neque porro quisquam est, qui dolorem ipsum quia dolor sit amet, consecte tur, adipisci velit, sed quia non numquam eius modi tempora.</p>
  </div>
  <div class="testimonial" style="left:640px">
    <div class="avatar" role="img" aria-label="Customer portrait"></div>
    <svg class="quote-mark" width="30" height="26" viewBox="0 0 30 26"><path d="M0,0h12v12l-6,14h-5l4-12h-5z M16,0h12v12l-6,14h-5l4-12h-5z" fill="#f39c1a"/></svg>
    <div class="t-title">GOOD CUSTOMER CARE</div>
    <div class="t-name">Tovah</div>
    <div class="stars">★★★★☆</div>
    <p class="t-text">Neque porro quisquam est, qui dolorem ipsum quia dolor sit amet, consecte tur, adipisci velit, sed quia non numquam eius modi tempora.</p>
  </div>
</section>

<footer class="band site-footer">
  <div class="footer-brand">M&amp;T Electric</div>
  <span class="social" style="left:158px" aria-label="Social link"></span>
  <span class="social" style="left:203px" aria-label="Social link"></span>
  <span class="social" style="left:250px" aria-label="Social link"></span>
  <span class="social" style="left:295px" aria-label="Social link"></span>
  <div class="v-rule" style="left:456px"></div>
  <div class="v-rule" style="left:760px"></div>

  <div class="footer-head" style="left:536px">QUICK LINKS</div>
  <ul class="quick-links">
    <li>Home</li><li>Gallery</li><li>Speciality Services</li><li>About</li><li>Services</li><li>Sitemap</li><li>Contact</li>
  </ul>

  <div class="footer-head" style="left:861px">CONTACT US</div>
  <div class="contact-item" style="top:112px">
    <svg width="40" height="40" viewBox="0 0 40 40"><circle cx="20" cy="20" r="18" fill="none" stroke="#fff" stroke-width="2"/><path d="M20,11a6,6 0 0 1 6,6c0,5-6,12-6,12s-6-7-6-12a6,6 0 0 1 6-6z" fill="none" stroke="#fff" stroke-width="2"/><circle cx="20" cy="17" r="2" fill="#fff"/></svg>
    <div class="contact-label">ADDRESS,</div>
    <div class="contact-value">218 Ridgeline Road, PO Box<br>4410, Ketchum, ID 83340</div>
  </div>
  <div class="contact-item" style="top:190px">
    <svg width="40" height="40" viewBox="0 0 40 40"><circle cx="20" cy="20" r="18" fill="none" stroke="#fff" stroke-width="2"/><rect x="15" y="11" width="10" height="18" rx="2" fill="none" stroke="#fff" stroke-width="2"/><circle cx="20" cy="26" r="1" fill="#fff"/></svg>
    <div class="contact-label">PHONE:</div>
    <div class="contact-value">(555) 014-2290</div>
  </div>
  <div class="contact-item" style="top:250px">
    <svg width="40" height="40" viewBox="0 0 40 40"><circle cx="20" cy="20" r="18" fill="#fff"/><rect x="12" y="14" width="16" height="12" fill="none" stroke="#2f2f2f" stroke-width="2"/><polyline points="12,14 20,21 28,14" fill="none" stroke="#2f2f2f" stroke-width="2"/></svg>
    <div class="contact-label">Mail:</div>
    <div class="contact-value">office@mandtelectric.example</div>
  </div>

  <div class="footer-rule"></div>
  <div class="copyright">Copyright © 2017 M &amp; T Electric. All Right Reserved</div>
</footer>

</body>
</html>
```